Book Cover for Lanterns Along the Quiet Threshold

I need a book cover for a 6 x 9 paperback titled Lanterns Along the Quiet Threshold Gathered from Research and Voices Dwelling in the Realm beyond Our Present Days. It has to do with consciousness, the mind, incarnation onto Earth, leaving Earth, and the life in the life after this life. I have an idea I'm providing with this description, but I am open to anything that would be striking and stimulating, whether with a book or not. I am the author, T. Morgan Wexley. I've added another background idea to see if anyone can do something with it and I've increased the budget.

```html
<!DOCTYPE html>
<html lang="en">
<head>
<meta charset="utf-8">
<title>Lanterns Along the Quiet Threshold — Book Cover</title>
<link href="https://fonts.googleapis.com/css2?family=Playfair+Display:wght@700;900&family=Cormorant+Garamond:wght@500;600&display=swap" rel="stylesheet">
<style>
  :root {
    --page: #ffffff;
    --sea-deep: #12304d;
    --sea-mid: #1f4f75;
    --sea-light: #3a7fa8;
    --ink-light: #ffffff;
  }
  html, body {
    margin: 0;
    padding: 0;
    width: 1200px;
    height: 1200px;
    overflow: hidden;
    background: var(--page);
  }
  .cover {
    position: absolute;
    left: 300px;
    top: 150px;
    width: 600px;
    height: 900px;
    overflow: hidden;
    color: var(--ink-light);
  }
  .cover-backdrop {
    position: absolute;
    inset: 0;
    background:
      radial-gradient(ellipse 60% 45% at 55% 48%, var(--sea-light) 0%, rgba(58,127,168,0) 70%),
      radial-gradient(ellipse 90% 80% at 50% 50%, var(--sea-mid) 0%, var(--sea-deep) 100%);
  }
  .title-main,
  .title-line,
  .title-end,
  .subtitle,
  .author {
    position: absolute;
    left: 0;
    width: 100%;
    text-align: center;
    margin: 0;
    white-space: nowrap;
  }
  .title-main {
    top: 78px;
    font-family: "Playfair Display", serif;
    font-weight: 900;
    font-size: 88px;
    line-height: 1;
    letter-spacing: 4px;
  }
  .title-line {
    top: 180px;
    font-family: "Playfair Display", serif;
    font-weight: 700;
    font-size: 38px;
    line-height: 1;
    letter-spacing: 1.5px;
  }
  .title-end {
    top: 214px;
    font-family: "Playfair Display", serif;
    font-weight: 900;
    font-size: 66px;
    line-height: 1;
    letter-spacing: 1px;
  }
  .question-mark {
    position: absolute;
    left: 190px;
    top: 338px;
    width: 240px;
    height: 290px;
  }
  .question-mark text {
    font-family: "Playfair Display", serif;
    font-weight: 900;
    fill: var(--ink-light);
  }
  .subtitle {
    top: 692px;
    font-family: "Cormorant Garamond", serif;
    font-weight: 600;
    font-size: 17px;
    line-height: 34px;
    letter-spacing: 5px;
    text-transform: uppercase;
  }
  .author {
    top: 826px;
    font-family: "Cormorant Garamond", serif;
    font-weight: 600;
    font-size: 31px;
    line-height: 1;
    letter-spacing: 4px;
    text-transform: uppercase;
  }
</style>
</head>
<body>
  <main class="cover">
    <div class="cover-backdrop" role="img" aria-label="Aerial photograph of deep blue ocean water with white foam and a small figure walking inside the question mark"></div>

    <h1 class="title-main">LANTERNS</h1>
    <p class="title-line">Along the Quiet</p>
    <p class="title-end">Threshold</p>

    <svg class="question-mark" viewBox="0 0 240 290" aria-hidden="true">
      <text x="120" y="272" text-anchor="middle" font-size="360">?</text>
    </svg>

    <p class="subtitle">Through Patient Inquiries<br>and Voices from Beyond</p>

    <p class="author">T. Morgan Wexley</p>
  </main>
</body>
</html>
```